Spring Detox sale graphics for social media

You MUST read the Brief in the WORD document and follow the instructions there. I want to create 10 social media graphics (new Instagram size 4:5 (1080 x 1350 pixels) focusing on our Mother’s Day Spring Detox Sale graphics, using any of the pics attached. Use the attached pics, NO RANDOM STOCK PHOTOGRAPHY. For the color scheme of the graphics, they should all be complementary to the product colors or feel like Spring time.

Target Market(s)

primarily women

Requirements
Must have
• the photos and text attached

```html
<!DOCTYPE html>
<html lang="en">
<head>
<meta charset="utf-8">
<title>Mother's Day Spring Detox Sale</title>
<link rel="stylesheet" href="https://fonts.googleapis.com/css2?family=Open+Sans:wght@400;600;700;800&family=Fira+Sans+Extra+Condensed:wght@400;600&family=Fira+Sans+Condensed:wght@600&display=swap">
<style>
  :root {
    --plum: #66213f;
    --pink: #e54896;
    --mauve: #b77aa6;
    --mint: #b4f2ea;
    --mint-soft: #dcf8f3;
    --blush: #fdf5f8;
    --white: #ffffff;
  }
  html, body { margin: 0; padding: 0; overflow: hidden; }
  .canvas {
    position: relative;
    width: 960px;
    height: 1200px;
    overflow: hidden;
    background: linear-gradient(180deg, var(--blush) 0%, #f3fbfa 30%, var(--mint-soft) 50%, var(--mint) 78%, #c8f5ef 100%);
    font-family: "Open Sans", sans-serif;
  }
  .floral-backdrop {
    position: absolute; inset: 0;
    background:
      radial-gradient(ellipse 260px 200px at 130px 90px, rgba(244, 200, 222, 0.45), transparent 70%),
      radial-gradient(ellipse 220px 180px at 840px 420px, rgba(200, 238, 232, 0.7), transparent 70%),
      radial-gradient(ellipse 300px 160px at 380px 540px, rgba(255, 255, 255, 0.5), transparent 70%),
      radial-gradient(ellipse 140px 90px at 40px 220px, rgba(150, 225, 225, 0.35), transparent 70%);
  }
  .dotted-glow {
    position: absolute; left: -60px; top: 700px; width: 260px; height: 380px;
    background: radial-gradient(ellipse at 30% 60%, rgba(255,255,255,0.85), rgba(255,255,255,0.25) 55%, transparent 75%);
  }
  .corner-rings { position: absolute; top: 0; right: 0; }
  .eyebrow {
    position: absolute; top: 56px; left: 0; width: 960px;
    text-align: center; margin: 0;
    font-family: "Open Sans", sans-serif; font-weight: 400;
    font-size: 40px; letter-spacing: 6px; color: var(--plum);
  }
  .sale-title {
    position: absolute; top: 112px; left: 0; width: 960px;
    text-align: center; margin: 0;
    font-family: "Fira Sans Condensed", sans-serif; font-weight: 600;
    font-size: 66px; letter-spacing: 4px; color: var(--pink);
  }
  .offer, .headline { position: absolute; left: 0; top: 0; }
  .offer text, .headline text { paint-order: stroke; stroke-linejoin: round; }
  .offer-number { font-family: "Open Sans", sans-serif; font-weight: 800; fill: var(--pink); stroke: var(--white); stroke-width: 5px; }
  .offer-percent, .offer-off { font-family: "Fira Sans Extra Condensed", sans-serif; font-weight: 400; fill: var(--pink); stroke: var(--white); stroke-width: 5px; }
  .headline text { font-family: "Fira Sans Condensed", sans-serif; font-weight: 600; fill: var(--plum); stroke: var(--white); stroke-width: 4px; }
  .pedestal { position: absolute; left: 0; top: 0; }
  .product-lineup {
    position: absolute; left: 102px; top: 653px; width: 782px; height: 458px;
    border-radius: 40px 40px 60px 60px;
    background:
      linear-gradient(180deg, rgba(255,255,255,0.9) 0%, rgba(255,255,255,0.55) 45%, rgba(255,255,255,0) 100%),
      linear-gradient(90deg, #aebfe6 0%, #cfe3da 30%, #f2b3b6 58%, #eab7d8 80%, #e9d3e4 100%);
  }
  .tagline {
    position: absolute; top: 1137px; left: 0; width: 960px; margin: 0;
    text-align: center; font-family: "Open Sans", sans-serif; font-weight: 400;
    font-size: 33px; letter-spacing: 2px; color: var(--plum);
  }
</style>
</head>
<body>
<main class="canvas">
  <div class="floral-backdrop" role="img" aria-label="Soft pale floral background pattern"></div>
  <div class="dotted-glow" role="img" aria-label="Soft white dotted texture"></div>

  <svg class="corner-rings" width="160" height="260" viewBox="0 0 160 260" aria-hidden="true">
    <circle cx="204" cy="115" r="140" fill="none" stroke="var(--mauve)" stroke-width="7"/>
    <circle cx="204" cy="115" r="119" fill="none" stroke="var(--mauve)" stroke-width="6"/>
  </svg>

  <p class="eyebrow">MOTHER’S DAY</p>
  <h2 class="sale-title">SPRING DETOX SALE</h2>

  <svg class="offer" width="960" height="500" viewBox="0 0 960 500" aria-label="25% off">
    <text class="offer-number" x="162" y="471" font-size="345" textLength="318" lengthAdjust="spacingAndGlyphs">25</text>
    <text class="offer-percent" x="478" y="464" font-size="330" textLength="236" lengthAdjust="spacingAndGlyphs">%</text>
    <text class="offer-off" x="692" y="320" font-size="124" textLength="170" lengthAdjust="spacingAndGlyphs">OFF</text>
  </svg>

  <svg class="headline" width="960" height="640" viewBox="0 0 960 640" aria-label="Refresh Your Body">
    <text x="48" y="602" font-size="132" textLength="872" lengthAdjust="spacingAndGlyphs">Refresh Your Body</text>
  </svg>

  <svg class="pedestal" width="960" height="1200" viewBox="0 0 960 1200" aria-hidden="true">
    <ellipse cx="480" cy="1090" rx="560" ry="62" fill="#ffffff" opacity="0.95"/>
  </svg>

  <div class="product-lineup" role="img" aria-label="Product photo: four white supplement bottles standing on a white pedestal"></div>

  <p class="tagline">Detox. Reset. Feel Amazing</p>
</main>
</body>
</html>
```